Manufacturer's Representative Group needs a clean new Website

We represent and sell a number of suppliers that design and build products used in Biopharmaceutical manufacturing. Our sales region is in the central US. Our customer base is scientific / engineering based - so clean, we organized design with a focus on the products - easy and clear navigation is necessary. We do not sell direct or warehouse product - so e-commerce is not needed. Our customers will use the website for reference on what we do and offer - we will use the site as a platform to present products from each vendor and the home page will be used to capture an overview and draw users deeper into the site. You can view our current site - which needs A LOT of help to get ideas on products represented and types of products

Target Market(s)

Engineers and Pharmaceutical / Bio pharm end users

Industry/Entity Type

E-Commerce

Number of Pages Required

2 page

Font styles to use
Sans Serif

Requirements
Must have
• I need a home page that provides a snapshot of my company and the product lines we represent - then a second page that I can copy as a template for each line I rep as well as for an "About us / contact" page.
• I would like to be able to manage content on the pages so something easy to adjust pictures or add content is a must
• Must use our logo

```html
<!DOCTYPE html>
<html lang="en">
<head>
<meta charset="utf-8">
<title>Prairie Bio</title>
<link href="https://fonts.googleapis.com/css2?family=Josefin+Sans:wght@400;600;700&family=Source+Sans+3:wght@400;600&family=Arimo:wght@400;700&display=swap" rel="stylesheet">
<style>
:root{
  --navy:#2a2466;
  --orange:#f15a24;
  --purple:#3d1f9e;
  --grey:#f1f1f1;
  --text:#333;
  --white:#fff;
}
*{box-sizing:border-box;margin:0;padding:0}
html,body{width:991px;height:1200px;overflow:hidden;background:var(--white)}
body{font-family:'Arimo',Arial,sans-serif;color:var(--text);position:relative}
.page{position:relative;width:991px;height:1200px}
.top-band{position:absolute;left:0;top:0;width:991px;height:361px;background:var(--navy);border-top:6px solid var(--orange)}
.header{position:absolute;left:83px;top:0;width:826px;height:98px;background:var(--white);border-radius:0 0 8px 8px}
.brand{position:absolute;left:12px;top:26px;display:flex;align-items:center;gap:10px;font-family:'Josefin Sans',sans-serif;font-weight:600;font-size:34px;color:var(--navy)}
.brand-dot{width:24px;height:24px;border-radius:50%;background:var(--orange)}
.call{position:absolute;right:10px;top:8px;font-family:'Josefin Sans',sans-serif;font-size:18px;color:var(--navy)}
.call span{color:var(--orange)}
.nav{position:absolute;left:535px;top:62px;display:flex;align-items:center;font-size:12px}
.nav a{text-decoration:none;color:#444;height:27px;line-height:27px;padding:0 16px;margin-right:12px}
.nav a.active{background:var(--orange);color:var(--white)}
.hero{position:absolute;left:83px;top:116px;width:826px;height:356px;background:var(--white);border-radius:8px;padding:6px;box-shadow:0 1px 3px rgba(0,0,0,.15)}
.hero-img{width:100%;height:100%;border-radius:4px;background:linear-gradient(90deg,#c9d6e2 0%,#e9eef3 35%,#b6bcc4 50%,#eef1f4 70%,#d7dde4 100%)}
.welcome{position:absolute;left:90px;top:493px;width:811px;text-align:center}
.welcome h1{font-family:'Source Sans 3',sans-serif;font-weight:400;font-size:27px;color:var(--navy);letter-spacing:.5px}
.welcome h1 span{color:var(--orange);font-weight:600}
.welcome p{font-family:'Source Sans 3',sans-serif;font-size:11px;line-height:18px;color:#444;margin-top:14px}
.products-band{position:absolute;left:0;top:662px;width:991px;height:310px;background:var(--grey)}
.section-title{position:absolute;left:89px;top:674px;font-family:'Josefin Sans',sans-serif;font-size:24px;color:var(--navy)}
.section-title span{color:var(--orange);font-weight:700}
.card{position:absolute;width:273px;height:114px;background:var(--white);padding:6px;display:flex;gap:8px}
.card-img{width:137px;height:102px;flex:none}
.card h3{font-family:'Josefin Sans',sans-serif;font-weight:600;font-size:14px;color:var(--navy);margin:5px 0 4px;letter-spacing:.5px}
.card p{font-size:10px;line-height:15px;color:#333}
.cta{position:absolute;left:673px;top:686px;width:235px;height:274px;background:var(--orange);padding:18px 8px 0 13px}
.cta h2{font-family:'Josefin Sans',sans-serif;font-weight:700;font-size:21px;color:var(--white);padding-bottom:6px;border-bottom:1px dotted rgba(255,255,255,.6)}
.field{display:block;width:207px;height:30px;background:#f7f7f7;border:2px solid #ddd;border-radius:10px;margin-top:12px;padding:0 14px;font-size:10px;line-height:26px;color:#555}
.field.area{height:67px;width:204px;margin-left:3px;line-height:16px;padding-top:6px}
.submit{position:absolute;right:14px;top:235px;width:92px;height:30px;background:var(--purple);border:2px solid var(--white);border-radius:10px;color:var(--white);font-size:10.5px;line-height:26px;text-align:center}
.companies{position:absolute;left:0;top:988px;width:991px;text-align:center}
.companies h2{font-family:'Josefin Sans',sans-serif;font-weight:400;font-size:24px;color:#333;letter-spacing:.5px}
.partners{position:absolute;left:97px;top:1037px;width:780px;display:flex;justify-content:space-between;align-items:center;height:58px}
.partner{font-family:'Arimo',sans-serif;font-weight:700;font-size:15px;color:var(--navy);display:flex;align-items:center;gap:6px}
.partner .mark{width:12px;height:12px;background:#9aa0b5;flex:none}
.footer{position:absolute;left:0;top:1115px;width:991px;height:85px;background:var(--navy);border-top:4px solid var(--orange);color:var(--white)}
.footer-links{position:absolute;left:89px;top:19px;font-size:12.5px}
.footer-links a{color:var(--white);text-decoration:none}
.footer-links .sep{margin:0 22px}
.copyright{position:absolute;left:89px;top:42px;font-size:12.5px}
.footer-brand{position:absolute;right:89px;top:22px;display:flex;align-items:center;gap:8px;font-family:'Josefin Sans',sans-serif;font-weight:600;font-size:28px;color:var(--white)}
.footer-brand .brand-dot{width:20px;height:20px;background:var(--white)}
</style>
</head>
<body>
<div class="page">
  <div class="top-band"></div>
  <header class="header">
    <div class="brand"><span class="brand-dot"></span>Prairie Bio</div>
    <div class="call"><span>Call Now</span> (555) 014-7626</div>
    <nav class="nav">
      <a class="active" href="#">HOME</a>
      <a href="#">CONTACT</a>
      <a href="#">PRODUCTS</a>
    </nav>
  </header>

  <section class="hero">
    <div class="hero-img" role="img" aria-label="Laboratory scientists working at a bioreactor control unit"></div>
  </section>

  <section class="welcome">
    <h1>WELCOME TO PRAIRIE <span>BIO</span></h1>
    <p><strong>Prairie Biosolutions</strong> is a distribution channel, licensed partner and manufacturers representative group providing high quality fluid handling products and technical services to the Midwestern biopharmaceutical community. With a core staff of experienced professionals and a team approach to all customer needs, we offer over 30 years of cGMP experience in the selection and use of most process consumable products.</p>
    <p>We're looking forward to working with you!</p>
  </section>

  <div class="products-band"></div>
  <h2 class="section-title">Our <span>Products</span></h2>

  <article class="card" style="left:83px;top:714px">
    <div class="card-img" role="img" aria-label="Coiled clear tubing" style="background:linear-gradient(135deg,#0d2a5a,#3f7fc0)"></div>
    <div><h3>Lorem Ipsum</h3><p>Prairie Biosolutions<br>is a distribution channel<br>licensed partner<br>and manufacturers<br>representative group</p></div>
  </article>
  <article class="card" style="left:377px;top:714px">
    <div class="card-img" role="img" aria-label="Blue peristaltic pump" style="background:linear-gradient(135deg,#4a78c0,#8a8f96)"></div>
    <div><h3>Lorem Ipsum</h3><p>Prairie Biosolutions<br>is a distribution channel,<br>licensed partner<br>and manufacturers<br>representative group</p></div>
  </article>
  <article class="card" style="left:83px;top:846px">
    <div class="card-img" role="img" aria-label="Red benchtop pump" style="background:linear-gradient(135deg,#c21f25,#e6d8c8)"></div>
    <div><h3>Lorem Ipsum</h3><p>Prairie Biosolutions<br>is a distribution channel,<br>licensed partner<br>and manufacturers<br>representative group</p></div>
  </article>
  <article class="card" style="left:377px;top:846px">
    <div class="card-img" role="img" aria-label="Modular cleanroom interior" style="background:linear-gradient(180deg,#d9dee2,#9aa3aa)"></div>
    <div><h3>Lorem Ipsum</h3><p>Prairie Biosolutions<br>is a distribution channel,<br>licensed partner<br>and manufacturers<br>representative group</p></div>
  </article>

  <aside class="cta">
    <h2>CALL TO ACTION</h2>
    <div class="field">Your Name</div>
    <div class="field">Your Email</div>
    <div class="field area">Additional Information</div>
    <div class="submit">Submit Form</div>
  </aside>

  <section class="companies">
    <h2>Companies Represented</h2>
  </section>
  <div class="partners">
    <div class="partner"><span class="mark"></span>Stonegate Polymers</div>
    <div class="partner">Arcflow Tubing</div>
    <div class="partner">Fillwise</div>
    <div class="partner">Finemark</div>
    <div class="partner">CleanSeal</div>
    <div class="partner">Modulab</div>
  </div>

  <footer class="footer">
    <div class="footer-links"><a href="#">Home</a><span class="sep">|</span><a href="#">Contact Us</a><span class="sep">|</span><a href="#">Products</a></div>
    <div class="copyright">© Prairie Biosolutions, Corp.</div>
    <div class="footer-brand"><span class="brand-dot"></span>Prairie Bio</div>
  </footer>
</div>
</body>
</html>
```